Letterhead Design for Law Firm

**Edit: I have added the photo of a bottom that I like.

------
We are looking for a re-design of our new letterhead. The letterhead is for a law firm and will be used for digital and traditionally printed correspondence.

Here are some suggestions:

- Please use colours are #8ec900 and simple black.
- Please do not use any type of "waves" at the bottom of the page. This is not in style at all.
- Please stay modern yet conservative.
- Please use font Segoe UI Light or similar if you can
- Avoid clipart or illustrations.
- Utilize ample white space in the layout so the design looks clean and information is easy to read at a glance. Don't overcrowd the letterhead.
- Make sure the letterhead design is consistent with our brand identity (see corvelith.ca)
-Please, no black headers or footers.

I am attaching my current letterhead and signature for your convenience.

Remember, the letterhead is an extension of our professional identity. We are a successful firm and trial lawyers who correspond with insurers, judges, lawyers, courts, clients, etc. Make it new, modern, attractive, yet powerful and conservative.

It needs to be easily printable. I would like the bleed removed in print so the black bar the bottom crosses the page (but the text is not near the edges)
Updates

Low design quality

Target Market(s)

Clients, Government Offices, Judiciary, Lawyers, Insurance Companies, Colleagues.

Industry/Entity Type

Law

Other font styles liked:
• Segoe UI LIght, Calibri Light,

Colors
00AB8E
00BBA5
67D7C9
C6EFE9
E9F9F6

Requirements
Must have
• Everything that is on the letterhead now.
Nice to have
• Cutting Edge design, yet conservative.
Should not have
• law firm cliche design, images,

```html
<!DOCTYPE html>
<html lang="en">
<head>
<meta charset="utf-8">
<title>Vantreel Letterhead</title>
<link rel="stylesheet" href="https://fonts.googleapis.com/css2?family=Arimo:wght@400;700&family=Questrial&display=swap">
<style>
  :root {
    --backdrop: #dcdcdc;
    --paper: #ffffff;
    --ink: #111111;
    --text: #5a5a5a;
    --accent: #8ec900;
    --signature-tone: #eeeeee;
  }
  * { box-sizing: border-box; margin: 0; padding: 0; }
  html, body {
    width: 1189px; height: 1200px; overflow: hidden;
    background: var(--backdrop);
  }
  .letterhead {
    position: absolute; left: 184px; top: 20px;
    width: 821px; height: 1160px;
    background: var(--paper);
    font-family: "Arimo", Arial, sans-serif;
    color: var(--text);
  }
  .brand-name {
    position: absolute; left: 0; right: 0; top: 48px;
    text-align: center;
    font-family: "Arimo", Arial, sans-serif;
    font-weight: 400; font-size: 42px; letter-spacing: 2px;
    color: var(--ink);
  }
  .salutation {
    position: absolute; left: 74px; top: 356px;
    font-family: "Questrial", "Century Gothic", sans-serif;
    font-weight: 700; font-size: 17.5px; color: #4d4d4d;
  }
  .letter-body {
    position: absolute; left: 73px; top: 409px; width: 675px;
    font-size: 13.3px; line-height: 17px;
  }
  .letter-body p { margin-bottom: 15px; }
  .closing {
    position: absolute; left: 74px; top: 758px;
    font-family: "Questrial", "Century Gothic", sans-serif;
    font-weight: 700; font-size: 10.5px; color: #444;
  }
  .signature {
    position: absolute; left: 487px; top: 860px;
    width: 246px; height: 56px;
    background: linear-gradient(90deg, var(--signature-tone), #f7f7f7);
  }
  .signatory { position: absolute; left: 487px; top: 929px; font-size: 12px; line-height: 15px; }
  .signatory-name { color: var(--accent); font-weight: 700; }
  .footer {
    position: absolute; left: 47px; top: 1104px; width: 726px; height: 30px;
    border-top: 1.5px solid var(--accent);
    border-bottom: 1.5px solid var(--accent);
    display: flex; align-items: center; justify-content: space-between;
    font-size: 11.4px; color: #555; white-space: nowrap;
  }
  .contact-item { display: inline-flex; align-items: center; gap: 4px; }
  .contact-item svg { width: 10px; height: 10px; fill: var(--accent); }
  .divider { margin: 0 2px; }
</style>
</head>
<body>
  <main class="letterhead">
    <div class="brand-name">VANTREEL</div>

    <h1 class="salutation">Dear Mr. Smith,</h1>

    <section class="letter-body">
      <p>Lorem ipsum dolor sit amet, consectetuer adipiscing elit, sed diam nonmmy nibh euismod tincidunt ut laor eet dolore magna aliquam erat volutpat. Ut wisi enim ad minim veniam, quis nostrud exerci tationmcorper suscipit lobortis nisl ut aliquip ex ea commodo consequat. Duis autem vel eum iriure dolor in hendrerit in vulputate velit esse molestie consequat, vel illum dolore eu feugiat</p>
      <p>Rorem ipsum dolor sit amet, consectetuer adipiscing elit, sed diam nonmmy nibh euismod tincidunt ut laor eet dolore magna aliquam erat volutpat. Ut wisi enim ad minim veniam, quis nostrud exerci tationmcorper suscipit lobortis nisl ut aliquip ex ea commodo consequat. Duis autem vel eum iriure dolor in hendrerit in vulputate velit esse molest</p>
      <p>Dorem ipsum dolor sit amet, consectetuer adipiscing elit, sed diam nonmmy nibh euismod tincidunt ut laor eet dolore magna aliquam erat volutpat. Ut wisi enim ad minim veniam, quis nostrud exerci tationmcorper suscipit lobortis nisl ut aliquip ex ea commodo consequat. Duis autem vel eum iriure dolor in hendrerit in suscipit lobortis nisl ut aliquip ex ea commodo consequat. Duis autem vel eum iriure dolor in hendrerit in vulputate velit esse molestie consequat, vel illum</p>
      <p>Sorem ipsum dolor sit amet, consectetuer adipiscing elit, sed diam nonmmy nibh euismod tincidunt ut laor eet dolore magna aliquam erat volutpat. Ut wisi enim ad minim veniam, quis nostrud exerci tationmcorper suscipit lobortis nisl ut aliquip ex ea commodo consequat. Duis autem vel eum iriure dolor in</p>
    </section>

    <div class="closing">Sincerely,</div>

    <div class="signature" role="img" aria-label="Handwritten signature of Ezra T. Vantreel"></div>

    <div class="signatory">
      <div class="signatory-name">Ezra T. Vantreel</div>
      <div class="signatory-firm">Vantreel Law Professional Corporation</div>
    </div>

    <footer class="footer">
      <span class="contact-item">
        <svg viewBox="0 0 10 10" aria-hidden="true"><path d="M2 0.5l1.6 2-1 1a6 6 0 0 0 3.9 3.9l1-1 2 1.6-1 1.5C4.5 9.5 0.5 5.5 0.5 1.5z"/></svg>
        905-555-0142
      </span>
      <span class="contact-item">
        <svg viewBox="0 0 10 10" aria-hidden="true"><path d="M0.5 2h9v6h-9z M1 2.5l4 3 4-3" stroke="#fff" stroke-width="0.8"/></svg>
        info@corvelith.ca
      </span>
      <span class="contact-item">
        <svg viewBox="0 0 10 10" aria-hidden="true"><circle cx="5" cy="5" r="4.5"/><path d="M0.5 5h9M5 0.5c-2 2.5-2 6.5 0 9M5 0.5c2 2.5 2 6.5 0 9" stroke="#fff" stroke-width="0.7" fill="none"/></svg>
        www.corvelith.ca <span class="divider">|</span> 48 Harlow Street East, Suite 1210, Hamilton, ON L8P 2B7, Canada
      </span>
    </footer>
  </main>
</body>
</html>
```